Letterhead Design Project

Letterhead for a Consultant Cardiologist in Adelaide Australia. Should be very classy, mature and imposing. I would prefer colours that portray confidence, gentleness and serenity.

The PDF attached is for you to see the details that will be on the letterhead and not the design which is extremely poor!

Target Market(s)

Health professionals especially medical doctors

Industry/Entity Type

Consultant

```html
<!DOCTYPE html>
<html lang="en">
<head>
<meta charset="utf-8">
<title>With Compliments – Dr Oluwasegun T. Ademiluyi</title>
<link rel="stylesheet" href="https://fonts.googleapis.com/css2?family=Open+Sans:wght@400;600;700&display=swap">
<style>
  :root {
    --navy: #1d5274;
    --red: #d5404b;
    --ink: #464646;
    --band: #9198a5;
    --paper: #ffffff;
    --backdrop: #e4e4e4;
  }
  * { margin: 0; padding: 0; box-sizing: border-box; }
  html, body { width: 1200px; height: 1000px; overflow: hidden; }
  body {
    background: var(--backdrop);
    font-family: "Open Sans", Arial, sans-serif;
    color: var(--ink);
    position: relative;
  }
  .slip {
    position: absolute;
    left: 96px; top: 265px;
    width: 964px; height: 453px;
    background: var(--paper);
  }
  .slip__band {
    position: absolute; left: 0; right: 0; bottom: 0;
    height: 22px; background: var(--band);
  }
  .rule-line {
    position: absolute; left: 39px; top: 110px;
    width: 765px; height: 3px;
    background: linear-gradient(90deg, rgba(213,64,75,0.1) 0%, rgba(213,64,75,0.75) 60%, var(--red) 100%);
  }
  .pulse-mark {
    position: absolute; left: 804px; top: 30px;
    width: 120px; height: 135px;
    background: linear-gradient(180deg, #f6d9db 0%, #efc0c4 50%, #f6d9db 100%);
  }
  .doctor {
    position: absolute; right: 215px; top: 74px;
    text-align: right;
  }
  .doctor__name {
    font-size: 20px; font-weight: 700; color: var(--navy);
    letter-spacing: 0.6px; white-space: nowrap;
  }
  .doctor__quals {
    margin-top: 24px;
    font-size: 15px; color: var(--ink); letter-spacing: 0.2px;
  }
  .doctor__role {
    margin-top: 3px;
    font-size: 15px; color: var(--red);
  }
  .compliments {
    position: absolute; left: 39px; top: 263px;
    font-size: 29px; font-weight: 400; letter-spacing: -0.8px;
    color: var(--navy); white-space: nowrap;
  }
  .compliments__accent { color: var(--red); }
  .locations {
    position: absolute; left: 0; top: 318px; width: 100%;
  }
  .location {
    position: absolute; top: 0;
    font-size: 11px; line-height: 15px; white-space: nowrap;
    font-style: normal;
  }
  .location__title {
    font-weight: 700; color: var(--red); letter-spacing: 0.3px;
  }
  .location__label { font-weight: 700; color: var(--navy); }
  .location--elm { left: 39px; }
  .location--northgate { left: 242px; }
  .location--heartwell { left: 542px; }
  .location--calder { left: 786px; }
  .divider {
    position: absolute; top: 5px; width: 1px; height: 100px;
    background: #8a8a8a;
  }
  .divider--1 { left: 214px; }
  .divider--2 { left: 513px; }
  .divider--3 { left: 752px; }
</style>
</head>
<body>
  <main class="slip">
    <div class="rule-line"></div>
    <div class="pulse-mark" role="img" aria-label="Heartbeat trace graphic"></div>

    <header class="doctor">
      <h1 class="doctor__name">DR&nbsp; OLUWASEGUN. T. ADEMILUYI</h1>
      <p class="doctor__quals">M.B.B.S, F.M.C.P, F.R.A.C.P</p>
      <p class="doctor__role">Cardiologist</p>
    </header>

    <h2 class="compliments">WITH <span class="compliments__accent">COMPLIMENTS</span></h2>

    <section class="locations">
      <address class="location location--elm">
        <div class="location__title">THE ELM SPECIALIST CENTRE</div>
        <div>48 Marlowe Road</div>
        <div>Kestrelton SA 5018</div>
        <div><span class="location__label">Tel:</span> 8231 4607</div>
        <div><span class="location__label">Fax:</span> 8231 4608</div>
        <div>Provider No: 518260LY</div>
      </address>
      <span class="divider divider--1"></span>
      <address class="location location--northgate">
        <div class="location__title">NORTHGATE HEART &amp; SPECIALIST CLINIC</div>
        <div>Wattlebrook Districts, Private Hospital</div>
        <div>12-18 Penfold Road, Ashvale Park SA 5109</div>
        <div><span class="location__label">Tel:</span> 8274 3120</div>
        <div><span class="location__label">Fax:</span> 8274 3121</div>
        <div><span class="location__label">Email:</span> cardiology@ngcsc.com.au</div>
        <div>Provider No: 518260KK</div>
      </address>
      <span class="divider divider--2"></span>
      <address class="location location--heartwell">
        <div class="location__title">HEARTWELL AT LINDEN PARK</div>
        <div>64 Carrington Place, Linden Park</div>
        <div>Heartwell at Brooksfield, Shop 21</div>
        <div>Brooksfield Village Shopping Centre</div>
        <div>Harbour Road, Brooksfield</div>
        <div><span class="location__label">Tel:</span> (08) 8360 4412</div>
        <div><span class="location__label">Fax:</span> (08) 8360 4413</div>
      </address>
      <span class="divider divider--3"></span>
      <address class="location location--calder">
        <div class="location__title">PORT CALDER HOSPITAL</div>
        <div>27 Hospital Road</div>
        <div>Port Calder 5702</div>
        <div><span class="location__label">Tel:</span> 8641 2290</div>
        <div><span class="location__label">Fax:</span> 8641 2291</div>
        <div>Provider No: 518260UB</div>
      </address>
    </section>

    <div class="slip__band"></div>
  </main>
</body>
</html>
```